Roofing Contractor business card redesign

I want to redesign my business card with a fresh, eye catching concept

Target Market(s)

Residential Roofing Clients, potential employees, and subcontractors.

Industry/Entity Type

Business

Colors

Designer to choose colors to be used in the design.

Requirements
Nice to have
• I just want something that's more pleasing to the eye. You can use a combination of either / or of my logos.

```html
<!DOCTYPE html>
<html lang="en">
<head>
<meta charset="utf-8">
<title>Fair Hands Builders – Business Card</title>
<link href="https://fonts.googleapis.com/css2?family=Oswald:wght@500&family=Work+Sans:wght@400;700&display=swap" rel="stylesheet">
<style>
  :root {
    --maroon: #45120e;
    --orange: #f5821f;
    --ink: #2b2220;
    --paper: #ffffff;
    --rule: #c9a98a;
    --backdrop: #2b2b2b;
  }
  * { margin: 0; padding: 0; box-sizing: border-box; }
  html, body { width: 1200px; height: 930px; overflow: hidden; background: var(--backdrop); }
  .stage { position: relative; width: 1200px; height: 930px; }
  .card {
    position: absolute; left: 278px; width: 644px; height: 368px;
    border-radius: 20px; overflow: hidden;
  }
  .card-front { top: 76px; background: var(--paper); font-family: "Work Sans", sans-serif; color: var(--ink); }
  .card-back { top: 486px; background: var(--maroon); }
  .wave { position: absolute; left: 0; top: 0; width: 644px; height: 140px; }
  .brand-mark {
    position: absolute; left: 35px; top: 92px; width: 150px;
    display: flex; flex-direction: column; align-items: center; gap: 10px;
  }
  .brand-dot { width: 70px; height: 70px; border-radius: 50%; background: var(--orange); }
  .brand-name {
    font-family: "Work Sans", sans-serif; font-weight: 700; font-size: 19px;
    line-height: 1.15; color: var(--maroon); text-align: center;
  }
  .person { position: absolute; right: 36px; top: 176px; text-align: right; }
  .person-name {
    font-family: "Oswald", sans-serif; font-weight: 500; font-size: 29px;
    letter-spacing: 1px; color: var(--orange); line-height: 1;
  }
  .person-title { font-size: 17px; line-height: 20px; margin-top: 5px; }
  .divider { position: absolute; left: 35px; right: 36px; top: 268px; border-top: 1px solid var(--rule); }
  .address { position: absolute; left: 35px; top: 302px; font-size: 17px; line-height: 20px; }
  .contacts { position: absolute; right: 36px; top: 278px; list-style: none; font-size: 17px; line-height: 20px; }
  .contacts li { display: flex; justify-content: flex-end; align-items: center; gap: 12px; }
  .contacts svg { width: 13px; height: 13px; }
  .back-brand {
    position: absolute; left: 0; right: 0; top: 130px;
    display: flex; align-items: center; justify-content: center; gap: 18px;
  }
  .back-dot { width: 86px; height: 86px; border-radius: 50%; background: var(--orange); flex: none; }
  .back-name {
    font-family: "Work Sans", sans-serif; font-weight: 700; font-size: 38px;
    line-height: 1.1; color: var(--paper);
  }
</style>
</head>
<body>
<main class="stage">
  <section class="card card-front">
    <svg class="wave" viewBox="0 0 644 140" aria-hidden="true">
      <path d="M0 52 C 40 30, 70 22, 98 22 C 200 22, 300 80, 400 112 C 470 132, 560 132, 644 100 L644 0 L0 0 Z" fill="var(--orange)"/>
      <path d="M0 46 C 40 24, 70 16, 98 16 C 200 16, 300 66, 400 96 C 470 116, 560 116, 644 88 L644 0 L0 0 Z" fill="var(--maroon)"/>
    </svg>

    <div class="brand-mark">
      <span class="brand-dot"></span>
      <span class="brand-name">Fair Hands<br>Builders, Inc.</span>
    </div>

    <div class="person">
      <h1 class="person-name">MARK ELLISON</h1>
      <p class="person-title">Apex Certified Roof Inspector<br>Licensed Property Adjuster</p>
    </div>

    <div class="divider"></div>

    <p class="address">4410 Cedar Hollow Road<br>Suite 118 Dallas, TX 75240</p>

    <ul class="contacts">
      <li>(555) 210-4830
        <svg viewBox="0 0 16 16" aria-hidden="true"><path d="M4 1 L6.5 4.5 L5 6.5 C6 8.5 7.5 10 9.5 11 L11.5 9.5 L15 12 L13 15 C7 14.5 1.5 9 1 3 Z" fill="none" stroke="var(--orange)" stroke-width="1.6" stroke-linejoin="round"/></svg>
      </li>
      <li>(555) 318-7062
        <svg viewBox="0 0 16 16" aria-hidden="true"><rect x="3.5" y="1" width="9" height="14" rx="1.5" fill="none" stroke="var(--orange)" stroke-width="1.6"/><line x1="7" y1="12.3" x2="9" y2="12.3" stroke="var(--orange)" stroke-width="1.4"/></svg>
      </li>
      <li>mark@fairhandsbuild.com
        <svg viewBox="0 0 16 16" aria-hidden="true"><rect x="1.5" y="3.5" width="13" height="9" rx="1" fill="none" stroke="var(--orange)" stroke-width="1.5"/><path d="M2 4 L8 9 L14 4" fill="none" stroke="var(--orange)" stroke-width="1.5"/></svg>
      </li>
    </ul>
  </section>

  <section class="card card-back">
    <div class="back-brand">
      <span class="back-dot"></span>
      <span class="back-name">Fair Hands<br>Builders, Inc.</span>
    </div>
  </section>
</main>
</body>
</html>
```